Powerpoint design template for LUMOTEX for new digital platform

We would like to use a PowerPoint template, we would like to create a new page, we would like to create a new digital platform LUMOTEX for schools and parents for the creation of playful communication and educational tools for children to enhance their positive development, amaze them learn in a playful way. This platform is going to be the most creative, stimulating and innovative classroom, easy to use and fast to implement. Scrapbooking, collages ... Magazine, newsletters Diplomla / awards Slideshows Facebook Calendars Organizers Greetings Games ... This powerpoint template will be used essential to We are looking for a professional design, positioning our brand in the children market with an adult hearing. so you will need to find a good deal. Primary target: nurseries & schools from 0 to 18 years old and universities (in 2nd phase) Secondary target: small & medium businesses Third target: general public, and TPE If it is a color scheme, then it is suggested that it be marketed in Europe (UK, Italy, Spain) and in a 2nd Stage USA and other countries. multiple options for front page, insidious pages (multiple styles with limited text and extended text) and final contact page We need something to read, we can not do it too much, but we can not do it. , and inside pages aligned to our logo

Target Market(s)

Target 1; Education with teacher Target 2; parents and grandparents

Industry/Entity Type

Education

Font styles to use
Other font styles liked:
• not decided. but not too fancy

Requirements
Must have
• Multi page options for front page, page insides (multiple styles with limited text and extended text) and final page contact
Nice to have
• do not have a lot of ideas. We need something to read, we can not get away from it
Should not have
• not too fancy and busy: keep clarity & simplicity while reassuring on quality

```html
<!DOCTYPE html>
<html lang="en">
<head>
<meta charset="utf-8">
<title>LUMOTEX – Content Slide</title>
<link href="https://fonts.googleapis.com/css2?family=Lato:wght@400;700&family=Nunito:wght@700;800;900&display=swap" rel="stylesheet">
<style>
  :root {
    --white: #ffffff;
    --brand-pink: #e6327f;
    --panel-blue: #0fa7e6;
    --panel-pink: #e92f82;
    --panel-orange: #f47b20;
    --panel-yellow: #fbba1d;
    --brand-dark: #2b2b2b;
    --brand-lime: #c5dc3a;
  }
  * { margin: 0; padding: 0; box-sizing: border-box; }
  html, body {
    width: 1200px;
    height: 900px;
    overflow: hidden;
    background: var(--white);
  }
  .slide {
    position: relative;
    width: 1200px;
    height: 900px;
    background: var(--white);
    font-family: "Lato", Arial, sans-serif;
    color: var(--white);
  }
  .slide-title {
    position: absolute;
    left: 21px;
    top: 26px;
    font-family: "Nunito", Arial, sans-serif;
    font-weight: 800;
    font-size: 39px;
    letter-spacing: 0.5px;
    color: var(--brand-pink);
  }
  .brand {
    position: absolute;
    right: 36px;
    top: 34px;
    display: flex;
    flex-direction: column;
    align-items: flex-start;
  }
  .brand-row {
    display: flex;
    align-items: center;
    gap: 10px;
  }
  .brand-mark {
    width: 26px;
    height: 26px;
    background: var(--brand-lime);
  }
  .brand-name {
    font-family: "Nunito", Arial, sans-serif;
    font-weight: 900;
    font-size: 40px;
    line-height: 1;
    color: var(--brand-dark);
  }
  .brand-tagline {
    margin-top: 6px;
    margin-left: 36px;
    font-family: "Lato", Arial, sans-serif;
    font-size: 10px;
    line-height: 1.15;
    letter-spacing: 1.5px;
    color: var(--brand-dark);
  }
  .section {
    position: absolute;
    width: 594px;
    padding: 78px 0 0 34px;
  }
  .section--blue   { left: 0;     top: 123px; height: 384px; background: var(--panel-blue); }
  .section--pink   { left: 606px; top: 123px; height: 384px; background: var(--panel-pink); }
  .section--orange { left: 0;     top: 519px; height: 381px; background: var(--panel-orange); padding-top: 86px; }
  .section--yellow { left: 606px; top: 519px; height: 381px; background: var(--panel-yellow); padding-top: 86px; }
  .section-title {
    font-weight: 700;
    font-size: 33px;
    line-height: 1.2;
    margin-bottom: 8px;
  }
  .section-text {
    font-size: 22.5px;
    line-height: 36px;
  }
  .step-badge {
    position: absolute;
    width: 66px;
    height: 66px;
    border-radius: 50%;
    border: 6px solid var(--white);
    display: flex;
    align-items: center;
    justify-content: center;
    font-family: "Nunito", Arial, sans-serif;
    font-weight: 900;
    font-size: 32px;
    color: var(--white);
  }
  .step-badge--1 { left: 238px; top: 87px;  background: var(--panel-blue); }
  .step-badge--2 { left: 840px; top: 87px;  background: var(--panel-pink); }
  .step-badge--3 { left: 238px; top: 485px; background: var(--panel-orange); }
  .step-badge--4 { left: 840px; top: 485px; background: var(--panel-yellow); }
</style>
</head>
<body>
<main class="slide">
  <h1 class="slide-title">CONTENT TITLE HERE</h1>

  <div class="brand">
    <div class="brand-row">
      <span class="brand-mark"></span>
      <span class="brand-name">LUMOTEX</span>
    </div>
    <p class="brand-tagline">YOUR TAGLINE<br>GOES HERE</p>
  </div>

  <section class="section section--blue">
    <h2 class="section-title">Section Title Here</h2>
    <p class="section-text">Lemon drops oat cake oat cake sugar plum<br>sweet gingerbread chocolate cake<br>gingerbread. Lemon drops oat cake oat cake<br>sugar plum sweet Lemon drops oat cake oat<br>cake sugar plum sweet gingerbread chocolate</p>
  </section>

  <section class="section section--pink">
    <h2 class="section-title">Section Title Here</h2>
    <p class="section-text">Lemon drops oat cake oat cake sugar plum<br>sweet gingerbread chocolate cake<br>gingerbread. Lemon drops oat cake oat cake<br>sugar plum sweet Lemon drops oat cake oat<br>cake sugar plum sweet gingerbread chocolate</p>
  </section>

  <section class="section section--orange">
    <h2 class="section-title">Section Title Here</h2>
    <p class="section-text">Lemon drops oat cake oat cake sugar plum<br>sweet gingerbread chocolate cake<br>gingerbread. Lemon drops oat cake oat cake<br>sugar plum sweet Lemon drops oat cake oat<br>cake sugar plum sweet gingerbread chocolate</p>
  </section>

  <section class="section section--yellow">
    <h2 class="section-title">Section Title Here</h2>
    <p class="section-text">Lemon drops oat cake oat cake sugar plum<br>sweet gingerbread chocolate cake<br>gingerbread. Lemon drops oat cake oat cake<br>sugar plum sweet Lemon drops oat cake oat<br>cake sugar plum sweet gingerbread chocolate</p>
  </section>

  <span class="step-badge step-badge--1">1</span>
  <span class="step-badge step-badge--2">2</span>
  <span class="step-badge step-badge--3">3</span>
  <span class="step-badge step-badge--4">4</span>
</main>
</body>
</html>
```